I need a SEO-friendly Wordpress website (making sure to style H1, H2, H3, etc correctly) for a Hawaii-based law firm called Meridian Crest Legal Group. Comparable websites include https://brvlaw.example/ and https://www.lomrit.example/ for design reference. The current copy on the TarnAdvocate.example website can be used.

```html
<!DOCTYPE html>
<html lang="en">
<head>
<meta charset="utf-8">
<title>Meridian Crest Legal Group — Divorce and Personal Injury Lawyers</title>
<link rel="stylesheet" href="https://fonts.googleapis.com/css2?family=Roboto:wght@400;500;700;900&family=Open+Sans:wght@400;600&display=swap">
<style>
:root{
  --accent:#b4571b;
  --accent-dark:#8f4313;
  --ink:#1d2733;
  --text:#4a4a4a;
  --muted:#8a8a8a;
  --light:#f0f0f0;
  --line:#e2e2e2;
  --dark:#262626;
  --darker:#1b1b1b;
  --social:#2f6fd6;
  --white:#fff;
}
*{box-sizing:border-box;margin:0;padding:0}
html,body{width:1200px;height:4092px;overflow:hidden}
body{font-family:"Open Sans",Arial,sans-serif;color:var(--text);background:var(--white);position:relative}
h1,h2,h3,h4{font-family:"Roboto",Arial,sans-serif;color:var(--ink)}
section,header,footer{position:absolute;left:0;width:1200px}
.abs{position:absolute}
.btn{display:inline-block;background:var(--accent);color:var(--white);font:700 12px "Roboto",sans-serif;letter-spacing:.5px;padding:9px 16px;text-transform:uppercase}
.section-title{position:absolute;left:0;width:1200px;text-align:center;font-size:30px;font-weight:700;text-transform:uppercase}
.section-title::after{content:"";display:block;width:50px;height:3px;background:var(--accent);margin:12px auto 0}

/* header */
.site-header{top:0;height:112px;background:var(--white);border-bottom:1px solid var(--line)}
.brand{left:132px;top:22px}
.brand-name{font:700 23px "Roboto",sans-serif;color:var(--ink)}
.brand-tag{font-size:15px;color:var(--text);margin-top:4px}
.follow{left:612px;top:22px;display:flex;align-items:center;gap:8px;font:700 12px "Roboto",sans-serif;color:var(--ink)}
.follow .dot{width:20px;height:20px;border-radius:50%;background:var(--social)}
.call{left:900px;top:14px}
.call small{font:700 11px "Roboto",sans-serif;color:var(--ink);display:block}
.call strong{font:700 23px "Roboto",sans-serif;color:var(--accent)}
.main-nav{left:612px;top:70px;display:flex;gap:26px;font:700 12px "Roboto",sans-serif;color:var(--ink)}
.main-nav a{padding-bottom:10px}
.main-nav a.active{color:var(--accent);border-bottom:2px solid var(--accent)}

/* hero */
.hero{top:112px;height:496px;background:linear-gradient(180deg,#4d7db0 0%,#2c4d73 40%,#1c2b40 70%,#7a5a3a 100%)}
.hero-caption{left:705px;top:170px;width:375px;background:rgba(20,24,30,.82);padding:22px 24px}
.hero-caption h1{color:var(--white);font-size:22px;line-height:1.25;text-transform:uppercase}
.hero-caption p{color:#ddd;font-size:14px;margin-top:8px;line-height:1.4}
.dots{left:0;width:1200px;top:462px;display:flex;justify-content:center;gap:10px}
.dots span{width:10px;height:10px;border-radius:50%;background:rgba(255,255,255,.55)}
.dots span.on{background:var(--white)}

/* about */
.about{top:608px;height:690px}
.about-photo{left:132px;top:32px;width:528px;height:460px;background:linear-gradient(135deg,#6b4a30,#2c2a30 60%,#8b6a48)}
.about-text{left:700px;top:70px;width:370px}
.about-text h4{font-size:16px;font-weight:700;text-transform:uppercase}
.about-text h2{font-size:34px;line-height:1.15;font-weight:900;text-transform:uppercase;margin:4px 0 22px}
.about-text p{font-size:14px;line-height:1.6;margin-bottom:16px}

/* practice */
.practice-title{top:1266px}
.practice{top:1360px;height:448px;background:linear-gradient(180deg,#2b2b2b,#1a1a1a 55%,#3a3530)}
.area{top:0;height:448px;text-align:center;padding-top:96px;color:var(--white)}
.area h3{color:var(--white);font-size:14px;font-weight:700;text-transform:uppercase;margin-top:18px;line-height:1.3}
.area.active{background:var(--accent)}
.area p{font-size:13px;line-height:1.5;color:#f4e2d6;margin:22px 28px 18px}
.area .more{font:700 12px "Roboto",sans-serif}

/* attorneys */
.attorneys{top:1820px;height:600px;background:var(--light)}
.attorneys .section-title{top:56px}
.card{top:168px;width:440px;height:300px;background:var(--white);box-shadow:0 2px 8px rgba(0,0,0,.08)}
.card .photo{position:absolute;left:20px;top:20px;width:180px;height:210px}
.card .bio{position:absolute;left:220px;top:22px;width:200px;font-size:13px;line-height:1.5}
.card .bio .btn{margin-top:14px;font-size:11px;padding:7px 12px}
.card h3{position:absolute;left:20px;top:246px;width:180px;text-align:center;font-size:12px;font-weight:700;text-transform:uppercase}

/* blog */
.blog{top:2420px;height:690px}
.blog .section-title{top:92px}
.posts{left:160px;top:196px;width:330px}
.post{border-bottom:1px solid var(--line);padding:18px 0 16px}
.post h3{font-size:17px;font-weight:700;text-transform:uppercase;line-height:1.3}
.post p{font-size:12px;line-height:1.5;margin:10px 0}
.post a{font:700 12px "Roboto",sans-serif;color:var(--accent);text-decoration:underline}
.blog-photo{left:512px;top:90px;width:548px;height:538px;background:linear-gradient(135deg,#2a2622,#51463c 50%,#d8d4ce 80%,#a09890)}

/* contact */
.contact{top:3110px;height:630px;background:linear-gradient(180deg,#d9d9d9,#eeeeee)}
.contact-photo{left:132px;top:20px;width:528px;height:580px;background:linear-gradient(135deg,#1f2e44,#5c6f86 55%,#c9b9a4)}
.contact-panel{left:700px;top:40px;width:380px;height:540px;background:rgba(255,255,255,.6);padding:20px}
.call-today{display:flex;gap:14px;align-items:center}
.call-today small{font:700 14px "Roboto",sans-serif;color:var(--ink);display:block}
.call-today strong{font:700 28px "Roboto",sans-serif;color:var(--accent)}
.contact-panel h4{font-size:14px;font-weight:700;text-transform:uppercase;margin:34px 0 20px}
.field{background:var(--white);border:1px solid var(--line);height:42px;margin-bottom:16px;padding:12px;font-size:11px;color:var(--muted);text-transform:uppercase}
.field.msg{height:96px}
.submit{display:block;text-align:center;background:var(--accent);color:var(--white);font:700 15px "Roboto",sans-serif;padding:14px;text-transform:uppercase}

/* footer */
.site-footer{top:3740px;height:300px;background:var(--dark);color:#bdbdbd}
.footer-brand{left:132px;top:90px}
.footer-brand .brand-name{color:var(--white);font-size:22px}
.footer-brand .brand-tag{color:#cfcfcf}
.fcol{top:36px}
.fcol h4{color:var(--white);font-size:12px;font-weight:700;text-transform:uppercase;margin-bottom:18px}
.fcol li{list-style:none;font-size:11px;line-height:1.6;margin-bottom:10px;display:flex;gap:10px;align-items:flex-start}
.fcol.menu li{margin-bottom:2px}
.fcol .ic{flex:none;width:18px;height:18px;border-radius:50%;background:#3d3d3d}
.fcol .sc{flex:none;width:20px;height:20px;border-radius:50%;background:var(--social)}
.copyright{top:4040px;height:52px;background:var(--darker);color:#9a9a9a;font-size:11px;text-align:center;line-height:52px}
</style>
</head>
<body>

<header class="site-header">
  <div class="abs brand">
    <div class="brand-name">Meridian Crest Legal Group</div>
    <div class="brand-tag">Divorce and Personal Injury Lawyers</div>
  </div>
  <div class="abs follow">FOLLOW US : <span class="dot"></span><span class="dot"></span></div>
  <div class="abs call"><small>CALL US NOW</small><strong>+1.808.555.0142</strong></div>
  <nav class="abs main-nav">
    <a class="active">HOME</a><a>PRACTICE AREAS</a><a>ATTORNEYS</a><a>BLOG</a><a>CONTACT US</a>
  </nav>
</header>

<section class="hero" role="img" aria-label="Coastal city skyline at dusk with a mountain behind and lights reflecting on the water">
  <div class="abs hero-caption">
    <h1>Kona Lawyers of MCLG – Legal Help With Love.</h1>
    <p>Over 70 years of combined practice, specializing in Personal Injury, Family &amp; Divorce, Child Custody.</p>
  </div>
  <div class="abs dots"><span></span><span></span><span class="on"></span><span></span><span></span></div>
</section>

<section class="about">
  <div class="abs about-photo" role="img" aria-label="Lawyer in a suit reading a book in front of a law library shelf"></div>
  <div class="abs about-text">
    <h4>About Us</h4>
    <h2>The Kona Lawyers of MCLG</h2>
    <p>The experienced attorneys in the Meridian Crest Legal Group's Kailua-Kona, Hawaii office provide clients with a wide range of litigation expertise, including legal claims involving divorce &amp; family, personal injury, toxic exposures, intellectual property, and real estate.</p>
    <p>Our Kona office also offers commercial and hospitality litigation expertise on behalf of a wide variety of clients, including restaurants, hotels, property owners, and many others.</p>
    <a class="btn">Read More</a>
  </div>
</section>

<h2 class="section-title practice-title">Areas of Practice</h2>
<section class="practice" aria-label="Areas of practice">
  <div class="abs area" style="left:132px;width:220px">
    <svg width="44" height="44" viewBox="0 0 44 44" fill="none" stroke="#fff" stroke-width="2.5"><circle cx="14" cy="10" r="5"/><circle cx="30" cy="10" r="5"/><path d="M6 38V24q0-6 8-6t8 6v14M22 38V24q0-6 8-6t8 6v14"/></svg>
    <h3>Family &amp; Divorce</h3>
  </div>
  <div class="abs area active" style="left:352px;width:256px">
    <svg width="44" height="44" viewBox="0 0 44 44" fill="none" stroke="#fff" stroke-width="2.5"><rect x="6" y="12" width="32" height="24" rx="2"/><path d="M16 12V7h12v5M22 18v12M16 24h12"/></svg>
    <h3>Personal Injury</h3>
    <p>Our Kona lawyers are well versed in injury law and have experience in all types of personal injury claims, including vehicle accidents, workplace harm, product defects, unsafe property, and wrongful death.</p>
    <span class="more">READ MORE</span>
  </div>
  <div class="abs area" style="left:608px;width:252px">
    <svg width="44" height="44" viewBox="0 0 44 44" fill="none" stroke="#fff" stroke-width="2.5"><circle cx="22" cy="16" r="10"/><path d="M22 26v12M17 38h10"/></svg>
    <h3>Corporate &amp;<br>Intellectual Property</h3>
  </div>
  <div class="abs area" style="left:860px;width:212px">
    <svg width="44" height="44" viewBox="0 0 44 44" fill="none" stroke="#fff" stroke-width="2.5"><path d="M4 22L22 6l18 16M10 18v20h24V18"/><rect x="18" y="26" width="8" height="12"/></svg>
    <h3>Real Estate</h3>
  </div>
</section>

<section class="attorneys">
  <h2 class="section-title">Our Attorneys</h2>
  <article class="abs card" style="left:140px">
    <div class="photo" role="img" aria-label="Portrait of attorney Dana Whitlock" style="background:linear-gradient(160deg,#7a3a2a,#2b2f3a)"></div>
    <div class="bio">Dana Whitlock graduated from Harbor State College of Law in 1972. She graduated magna cum laude from Harbor State College of Law in 2006, receiving an LLM degree in international law.<br><a class="btn">Read More</a></div>
    <h3>Dana Whitlock, Esq.</h3>
  </article>
  <article class="abs card" style="left:620px">
    <div class="photo" role="img" aria-label="Portrait of attorney Rowan Ellery" style="background:linear-gradient(160deg,#3c4a3a,#6f7b7e)"></div>
    <div class="bio">Rowan Ellery graduated from Harbor State College of Law in 1975. He has over 10 years of experience as a litigator in both State and Federal courts, primarily as a personal injury lawyer.<br><a class="btn">Read More</a></div>
    <h3>Rowan Ellery, Esq.</h3>
  </article>
</section>

<section class="blog">
  <h2 class="section-title">Latest Blog</h2>
  <div class="abs posts">
    <article class="post">
      <h3>Top 10 Things to Do Before Filing for Divorce</h3>
      <p>No one gets married with the intention of things not working out, but it's an unfortunate fact that many marriages don't work out in the end.</p>
      <a>READ MORE</a>
    </article>
    <article class="post">
      <h3>Top 10 Things to Do During Custody Battle</h3>
      <p>It's always tragic enough when two people who planned on spending their lives together no longer wish to see that dream through.</p>
      <a>READ MORE</a>
    </article>
    <article class="post" style="border-bottom:0">
      <h3>Lorem Ipsum Is Simply Dummy Text of the Printing</h3>
      <p>It's always tragic enough when two people who planned on spending their lives together no longer wish to see that dream through.</p>
      <a>READ MORE</a>
    </article>
  </div>
  <div class="abs blog-photo" role="img" aria-label="Hands signing a legal document with a pen on a desk"></div>
</section>

<section class="contact">
  <div class="abs contact-photo" role="img" aria-label="Two people in suits shaking hands across a table"></div>
  <div class="abs contact-panel">
    <div class="call-today">
      <svg width="30" height="30" viewBox="0 0 24 24" fill="#1d2733"><path d="M6.6 10.8a15 15 0 006.6 6.6l2.2-2.2a1 1 0 011-.25 11.4 11.4 0 003.6.57 1 1 0 011 1V20a1 1 0 01-1 1A17 17 0 013 4a1 1 0 011-1h3.5a1 1 0 011 1c0 1.25.2 2.45.57 3.57a1 1 0 01-.25 1z"/></svg>
      <div><small>CALL US TODAY</small><strong>+1.808.555.0142</strong></div>
    </div>
    <h4>Reach Out To Us</h4>
    <div class="field">Name</div>
    <div class="field">Email</div>
    <div class="field">Subject</div>
    <div class="field msg">Message</div>
    <a class="submit">Submit</a>
  </div>
</section>

<footer class="site-footer">
  <div class="abs footer-brand">
    <div class="brand-name">Meridian Crest Legal Group</div>
    <div class="brand-tag">Divorce and Personal Injury Lawyers</div>
  </div>
  <div class="abs fcol" style="left:520px;width:180px">
    <h4>Contact Us</h4>
    <ul>
      <li><span class="ic"></span>74-210 Palani Road, Suite 12, Kailua-Kona, HI 96740</li>
      <li><span class="ic"></span>+1.808.555.0142</li>
      <li><span class="ic"></span>hello@meridiancrest.example</li>
    </ul>
  </div>
  <div class="abs fcol menu" style="left:730px;width:120px">
    <h4>Menu</h4>
    <ul><li>HOME</li><li>PRACTICE AREAS</li><li>ATTORNEYS</li><li>BLOG</li><li>CONTACT US</li></ul>
  </div>
  <div class="abs fcol" style="left:880px;width:190px">
    <h4>Connect With Us</h4>
    <ul>
      <li><span class="sc"></span>Community</li>
      <li><span class="sc"></span>Updates</li>
      <li><span class="sc"></span>Network</li>
    </ul>
  </div>
</footer>
<div class="abs copyright" style="left:0;width:1200px">Copyright © 2019 All Rights Reserved</div>

</body>
</html>
```